R7M Horizon Business Card Design

We need a business card created for our New Business "R7M Horizon"<br/><br/>The business card design is up to you however the following information must be on the business card:<br/><br/>Front of the business card -<br/>Email :darrenp@r7mhorizon.nz<br/>Mobile: +64 (0) 22 4870 619<br/>Website: www.r7mhorizon.nz<br/>Card Owner Name: Darren Paltrow<br/>Company Title: Business Development Manager<br/>Slogan: "The BEST of both worlds". <br/>Logo On the front attached to the design brief<br/><br/>On the back: <br/>Space on the back for 4 more versions of the logo across the bottom of the card indicating different subsidiary brands - R7M Coffee, R7M Arts, R7M ?? (The card will be used for all of these brands - We Will add the extra subsidiary logos to the design once the design is finished (We are a graphics design team). <br/><br/>Other than that we want a premium feeling logo that remains universally usable depending on the business entity that we are using the card for. The use of bright bold colours would be great but we still want the card to feel premium.
Target Market(s)
Gift Design and Manufacturing Companies
Contact Information for Business Card
Front of the business card -
Email :darrenp@r7mhorizon.nz
Mobile: +64 (0) 22 4870 619
Website: www.r7mhorizon.nz
Card Owner Name: Darren Paltrow
Company Title: Business Development Manager
Slogan: "The BEST of both worlds".
Logo On the front attached to the design brief

```html
<!DOCTYPE html>
<html lang="en">
<head>
<meta charset="utf-8">
<title>R7M Horizon – Business Card</title>
<link rel="stylesheet" href="https://fonts.googleapis.com/css2?family=Michroma&family=Open+Sans:wght@400;600;700&display=swap">
<style>
  :root {
    --brand-blue: #2f3f9e;
    --brand-blue-deep: #26348a;
    --ink: #2b2b2b;
    --paper: #ffffff;
    --paper-shade: #eeeeee;
    --backdrop: #d9dbe0;
    --silver: #d8d8dc;
  }
  * { box-sizing: border-box; margin: 0; padding: 0; }
  html, body { width: 1200px; height: 900px; overflow: hidden; }
  body {
    background: var(--backdrop);
    font-family: "Open Sans", Arial, sans-serif;
    color: var(--ink);
    position: relative;
  }
  .card {
    position: absolute;
    left: 250px;
    width: 700px;
    height: 400px;
    box-shadow: 0 10px 30px rgba(0,0,0,0.25);
  }
  /* Front */
  .card-front {
    top: 40px;
    background: radial-gradient(ellipse at 60% 40%, var(--paper) 55%, var(--paper-shade) 100%);
  }
  .brand-name {
    position: absolute;
    font-weight: 700;
    color: var(--brand-blue);
    white-space: nowrap;
  }
  .card-front .brand-name {
    left: 40px;
    top: 172px;
    width: 260px;
    text-align: center;
    font-size: 34px;
    line-height: 44px;
  }
  .divider {
    position: absolute;
    left: 322px;
    top: 110px;
    width: 2px;
    height: 180px;
    background: var(--brand-blue);
  }
  .details {
    position: absolute;
    left: 348px;
    top: 112px;
    width: 330px;
  }
  .holder-name {
    font-family: "Michroma", "Open Sans", sans-serif;
    font-weight: 400;
    font-size: 19px;
    letter-spacing: 0.5px;
    color: var(--brand-blue);
    text-transform: uppercase;
    -webkit-text-stroke: 0.8px var(--brand-blue);
    line-height: 1.2;
    white-space: nowrap;
  }
  .holder-title {
    font-size: 16px;
    margin-top: 4px;
    white-space: nowrap;
  }
  .contact-list { list-style: none; margin-top: 12px; }
  .contact-list li {
    display: flex;
    align-items: center;
    gap: 10px;
    font-size: 16px;
    line-height: 26px;
    white-space: nowrap;
  }
  .contact-list svg { width: 14px; height: 14px; flex: none; }
  .slogan {
    font-size: 16px;
    margin-top: 6px;
    white-space: nowrap;
  }
  .slogan strong { color: var(--brand-blue); font-weight: 700; }

  /* Back */
  .card-back {
    top: 470px;
    background: linear-gradient(135deg, var(--brand-blue) 0%, var(--brand-blue-deep) 100%);
  }
  .card-back .brand-name {
    left: 0; right: 0;
    top: 140px;
    text-align: center;
    font-size: 54px;
    line-height: 70px;
    color: var(--silver);
  }
  .back-web {
    position: absolute;
    left: 0; right: 0;
    top: 300px;
    text-align: center;
    font-size: 18px;
    letter-spacing: 1px;
    color: var(--silver);
  }
</style>
</head>
<body>
  <section class="card card-front" aria-label="Business card front">
    <p class="brand-name">R7M Horizon</p>
    <div class="divider"></div>
    <div class="details">
      <h1 class="holder-name">Darren Paltrow</h1>
      <p class="holder-title">Business Development Manager</p>
      <ul class="contact-list">
        <li>
          <svg viewBox="0 0 24 24" aria-hidden="true"><path fill="#2f3f9e" d="M6.6 10.8a15 15 0 0 0 6.6 6.6l2.2-2.2a1 1 0 0 1 1-.25 11.4 11.4 0 0 0 3.6.57 1 1 0 0 1 1 1V20a1 1 0 0 1-1 1A17 17 0 0 1 3 4a1 1 0 0 1 1-1h3.5a1 1 0 0 1 1 1 11.4 11.4 0 0 0 .57 3.6 1 1 0 0 1-.25 1z"/></svg>
          <span>+64 (0) 22 4870 619</span>
        </li>
        <li>
          <svg viewBox="0 0 24 24" aria-hidden="true"><rect x="2.5" y="5" width="19" height="14" rx="1.5" fill="none" stroke="#2f3f9e" stroke-width="2"/><path d="M3 6l9 7 9-7" fill="none" stroke="#2f3f9e" stroke-width="2"/></svg>
          <span>darrenp@r7mhorizon.nz</span>
        </li>
        <li>
          <svg viewBox="0 0 24 24" aria-hidden="true"><circle cx="12" cy="12" r="9.5" fill="none" stroke="#2f3f9e" stroke-width="2"/><ellipse cx="12" cy="12" rx="4" ry="9.5" fill="none" stroke="#2f3f9e" stroke-width="1.6"/><path d="M2.5 12h19M4 7h16M4 17h16" stroke="#2f3f9e" stroke-width="1.6"/></svg>
          <span>www.r7mhorizon.nz</span>
        </li>
      </ul>
      <p class="slogan">The <strong>BEST</strong> of both worlds</p>
    </div>
  </section>

  <section class="card card-back" aria-label="Business card back">
    <p class="brand-name">R7M Horizon</p>
    <p class="back-web">www.r7mhorizon.nz</p>
  </section>
</body>
</html>
```